Walk Beside The River

Business Card design

Target Market(s)

People who require support in the commnity

Industry/Entity Type

Mental Health Support

Contact Information for Business Card

Mental Health Support Rosalind Tavener walkbesidetheriver@mailcove.com.au 0481 637 092 PO Box 926 Kelmara Heads 4599

Colors
6B429C
8869AF
B7A5CE
E3DAEB
F3F0F8

Requirements
Must have
• Logo & details listed above
Should not have
• No red or orange

```html
<!DOCTYPE html>
<html lang="en">
<head>
<meta charset="utf-8">
<title>Walk Beside The River – Business Card</title>
<link rel="stylesheet" href="https://fonts.googleapis.com/css2?family=Montserrat:wght@800&family=Open+Sans:wght@400;600&display=swap">
<style>
  :root {
    --stage: #232323;
    --card-dark: #1f1e24;
    --purple: #6b429c;
    --purple-mid: #8869af;
    --purple-deep: #5a3590;
    --lilac: #b7a5ce;
    --yellow: #f2e52a;
    --white: #ffffff;
  }
  * { margin: 0; padding: 0; box-sizing: border-box; }
  html, body { width: 1200px; height: 780px; overflow: hidden; background: var(--stage); }
  .stage {
    position: relative;
    width: 1200px;
    height: 780px;
    display: flex;
    justify-content: center;
    align-items: center;
    gap: 90px;
  }
  .card {
    position: relative;
    width: 320px;
    height: 600px;
    border-left: 4px solid var(--yellow);
    overflow: hidden;
  }
  /* Front */
  .card--front { background: var(--purple); }
  .front-pattern {
    position: absolute;
    inset: 0;
    background:
      radial-gradient(ellipse at 0% 0%, rgba(183,165,206,0.55) 0%, rgba(183,165,206,0) 45%),
      linear-gradient(160deg, var(--purple-mid) 0%, var(--purple) 45%, var(--purple-deep) 100%);
  }
  .front-brand {
    position: absolute;
    top: 58px;
    right: 36px;
    display: flex;
    align-items: center;
    gap: 8px;
  }
  .brand-dot {
    width: 14px;
    height: 14px;
    border-radius: 50%;
    background: var(--yellow);
    flex: none;
  }
  .brand-name {
    font-family: "Open Sans", sans-serif;
    font-weight: 600;
    font-size: 12px;
    letter-spacing: 0.14em;
    text-transform: uppercase;
    color: var(--white);
    line-height: 1.35;
    width: 110px;
  }
  /* Back */
  .card--back { background: var(--card-dark); }
  .back-brand {
    position: absolute;
    top: 70px;
    left: 0;
    right: 0;
    display: flex;
    flex-direction: column;
    align-items: center;
    gap: 14px;
  }
  .back-brand .brand-dot { width: 110px; height: 110px; background: var(--purple); }
  .back-brand .brand-name {
    width: auto;
    font-size: 14px;
    color: var(--white);
    text-align: center;
  }
  .holder {
    position: absolute;
    left: 34px;
    right: 24px;
    bottom: 70px;
    font-family: "Open Sans", sans-serif;
    color: var(--white);
  }
  .holder-name {
    font-family: "Montserrat", sans-serif;
    font-weight: 800;
    font-size: 27px;
    line-height: 1.1;
  }
  .holder-name .first { color: var(--yellow); }
  .holder-name .last { color: var(--purple-mid); }
  .holder-title {
    font-size: 14px;
    margin: 4px 0 30px 60px;
  }
  .holder-org { font-size: 13px; line-height: 1.45; margin-bottom: 18px; }
  .contact-list { list-style: none; font-size: 12.5px; }
  .contact-list li {
    display: flex;
    align-items: center;
    gap: 9px;
    line-height: 1.9;
    white-space: nowrap;
  }
  .contact-icon { width: 13px; height: 13px; flex: none; fill: var(--yellow); }
</style>
</head>
<body>
<main class="stage">
  <section class="card card--front" aria-label="Card front">
    <div class="front-pattern" role="img" aria-label="Purple star pattern fading to a soft lilac glow in the top-left corner"></div>
    <div class="front-brand">
      <span class="brand-dot"></span>
      <span class="brand-name">Walk Beside The River</span>
    </div>
  </section>

  <section class="card card--back" aria-label="Card back">
    <div class="back-brand">
      <span class="brand-dot"></span>
      <span class="brand-name">Walk Beside The River</span>
    </div>

    <div class="holder">
      <p class="holder-name"><span class="first">Dana</span> <span class="last">Vorlickova</span></p>
      <p class="holder-title">CEO/Director</p>
      <p class="holder-org">Mental Health Support<br>Rosalind Tavener</p>
      <ul class="contact-list">
        <li>
          <svg class="contact-icon" viewBox="0 0 24 24" aria-hidden="true"><path d="M6.6 10.8a15.1 15.1 0 0 0 6.6 6.6l2.2-2.2c.3-.3.7-.4 1-.2 1.1.4 2.3.6 3.6.6.6 0 1 .4 1 1V20c0 .6-.4 1-1 1A17 17 0 0 1 3 4c0-.6.4-1 1-1h3.5c.6 0 1 .4 1 1 0 1.3.2 2.5.6 3.6.1.3 0 .7-.2 1z"/></svg>
          <span>0481 637 092</span>
        </li>
        <li>
          <svg class="contact-icon" viewBox="0 0 24 24" aria-hidden="true"><path d="M2 5h20v14H2zm2 2v.5l8 5 8-5V7zm0 2.8V17h16V9.8l-8 5z"/></svg>
          <span>walkbesidetheriver@mailcove.com.au</span>
        </li>
        <li>
          <svg class="contact-icon" viewBox="0 0 24 24" aria-hidden="true"><path d="M12 2a7 7 0 0 0-7 7c0 5 7 13 7 13s7-8 7-13a7 7 0 0 0-7-7zm0 9.5A2.5 2.5 0 1 1 12 6.5a2.5 2.5 0 0 1 0 5z"/></svg>
          <span>PO Box 926 Kelmara Heads 4599</span>
        </li>
      </ul>
    </div>
  </section>
</main>
</body>
</html>
```